I need a business card for my dumpster rentals business

We need a business card for a roll off dumpster business. We drop off the dumpster the customers fills it and we pick up and dispose of the materials. We want it simple but to the point. We will send images of what we like. We want black and red for the colors. We want stated on the card, (We bring it/ You fill it/ We dump it) uploaded some ideas I have came up with

```html
<!DOCTYPE html>
<html lang="en">
<head>
<meta charset="utf-8">
<title>Redline Haul Dumpster Rentals – Business Card</title>
<link href="https://fonts.googleapis.com/css2?family=Open+Sans:wght@400;600;700&display=swap" rel="stylesheet">
<style>
  :root {
    --brand-red: #e11b22;
    --ink: #111111;
    --paper: #f4f4f4;
    --backdrop: #232323;
    --white: #ffffff;
  }
  * { box-sizing: border-box; margin: 0; padding: 0; }
  html, body { width: 1200px; height: 780px; overflow: hidden; }
  body {
    background: var(--backdrop);
    font-family: "Open Sans", Arial, sans-serif;
    position: relative;
  }
  .card {
    position: absolute;
    top: 240px;
    width: 525px;
    height: 300px;
    border-radius: 18px;
    overflow: hidden;
  }
  .card-front { left: 50px; background: var(--paper); }
  .card-back { left: 625px; background: var(--brand-red); }

  /* front */
  .brand {
    position: absolute;
    left: 34px;
    top: 52px;
    display: flex;
    align-items: flex-start;
    gap: 8px;
    width: 210px;
  }
  .brand-dot {
    width: 14px; height: 14px;
    border-radius: 50%;
    background: var(--brand-red);
    flex: none;
    margin-top: 10px;
  }
  .brand-name {
    font-weight: 700;
    font-size: 26px;
    line-height: 1.05;
    color: var(--ink);
    white-space: nowrap;
  }
  .brand-name small {
    display: block;
    font-size: 10px;
    font-weight: 600;
    letter-spacing: 3px;
    text-transform: uppercase;
    color: var(--brand-red);
    margin-top: 5px;
  }
  .divider {
    position: absolute;
    left: 0; top: 0;
  }
  .person {
    position: absolute;
    left: 284px;
    top: 86px;
  }
  .person-name {
    font-weight: 700;
    font-size: 27px;
    line-height: 1;
    color: var(--ink);
    white-space: nowrap;
  }
  .person-name .first { color: var(--brand-red); }
  .person-title {
    font-size: 13px;
    font-weight: 600;
    color: var(--ink);
    margin-top: 4px;
  }
  .contacts {
    list-style: none;
    margin-top: 16px;
  }
  .contacts li {
    display: flex;
    align-items: center;
    gap: 8px;
    font-size: 13px;
    color: var(--ink);
    line-height: 1.65;
  }
  .contacts svg { width: 13px; height: 13px; flex: none; }
  .address-band {
    position: absolute;
    left: 0; bottom: 0;
    width: 100%;
    height: 30px;
    background: var(--brand-red);
    color: var(--white);
    font-size: 13px;
    display: flex;
    align-items: center;
    padding-left: 26px;
  }
  .band-mark {
    position: absolute;
    right: 64px;
    bottom: 5px;
    width: 20px; height: 20px;
    border-radius: 50%;
    background: var(--white);
  }
  .band-end {
    position: absolute;
    right: 0; bottom: 0;
    width: 44px; height: 30px;
    background: var(--ink);
  }

  /* back */
  .back-brand {
    position: absolute;
    left: 30px;
    top: 30px;
    font-weight: 700;
    font-size: 18px;
    line-height: 1.05;
    color: var(--white);
  }
  .back-brand small {
    display: block;
    font-size: 8px;
    letter-spacing: 3px;
    text-transform: uppercase;
    margin-top: 3px;
  }
  .service-steps {
    position: absolute;
    left: 30px;
    bottom: 30px;
    font-size: 16px;
    font-weight: 600;
    color: var(--white);
    white-space: nowrap;
  }
</style>
</head>
<body>

<section class="card card-front" aria-label="Business card front">
  <svg class="divider" width="525" height="300" aria-hidden="true">
    <line x1="262" y1="230" x2="262" y2="70" stroke="#e11b22" stroke-width="1"/>
  </svg>

  <div class="brand">
    <span class="brand-dot" aria-hidden="true"></span>
    <p class="brand-name">Redline Haul<small>Dumpster Rentals</small></p>
  </div>

  <div class="person">
    <h1 class="person-name"><span class="first">Tomas</span> Verrick</h1>
    <p class="person-title">Managing Director</p>
    <ul class="contacts">
      <li>
        <svg viewBox="0 0 24 24" aria-hidden="true"><path fill="#e11b22" d="M6.6 10.8a15 15 0 0 0 6.6 6.6l2.2-2.2a1 1 0 0 1 1-.25 11.4 11.4 0 0 0 3.6.57 1 1 0 0 1 1 1V20a1 1 0 0 1-1 1A17 17 0 0 1 3 4a1 1 0 0 1 1-1h3.5a1 1 0 0 1 1 1c0 1.25.2 2.45.57 3.57a1 1 0 0 1-.25 1z"/></svg>
        (555) 014-2290
      </li>
      <li>
        <svg viewBox="0 0 24 24" aria-hidden="true"><rect x="2" y="5" width="20" height="14" rx="2" fill="#e11b22"/><path d="M3 6l9 7 9-7" fill="none" stroke="#fff" stroke-width="1.6"/></svg>
        info@redlinehaul.com
      </li>
      <li>
        <svg viewBox="0 0 24 24" aria-hidden="true"><circle cx="12" cy="12" r="10" fill="#e11b22"/><path d="M2 12h20M12 2c3 3 3 17 0 20M12 2c-3 3-3 17 0 20" fill="none" stroke="#fff" stroke-width="1.3"/></svg>
        www.redlinehaul.com
      </li>
    </ul>
  </div>

  <div class="address-band">1480 Maple Ridge Rd. Suite 120 Denton, TX 76201</div>
  <span class="band-mark" aria-hidden="true"></span>
  <span class="band-end" aria-hidden="true"></span>
</section>

<section class="card card-back" aria-label="Business card back">
  <p class="back-brand">Redline Haul<small>Dumpster Rentals</small></p>
  <p class="service-steps">We bring it / You fill it / We dump it</p>
</section>

</body>
</html>
```